Lumora Drink Mix Packaging Design

We need a packaging design for our new product called "Lumora Drink Mix." This drink mix can help prevent hangovers or lessen their severity if consumed after a night of drinking. Our tagline is: "Feel as good tomorrow morning as you do tonight." Our website is www.lumoradrinkmix-example.com. We are looking for a design that includes an outer box that contains individual serving packets and the packets themselves. Background color should be black and the colors should be vibrant. Our website uses bright blues, pinks, and purples reminiscent of colors under a blacklight (think club). Our target audience is 30-35 year-old people that occasionally party like they're still 18-21, but then regret it the following day. Please reference our website for additional information on the product.

Target Market(s)

Target market is 30-35 year old men and women that occasionally drink like they're still 18-21.

Industry/Entity Type

Product

Requirements
Must have
• Project must include a box that can hold ~5 individual serving packets inside, as well as the packets inside. Box must contain nutritional information and obligatory NQB disclaimer on one panel, as must the back of the single-serving packets. Package must be black as background with vibrant colors that "pop" and catch someone's eye. Package must include the product name "Lumora Drink Mix." Package must include the company name "Lumora Products, Inc."
Nice to have
• It should convey fun, friendship, partying, but also safety. Ideally, the tagline: "Feel as good tomorrow morning as you do tonight" should be somewhere on the packaging.
Should not have
• Pictures of people.

```html
<!DOCTYPE html>
<html lang="en">
<head>
<meta charset="utf-8">
<title>Lumora Drink Mix – Packaging</title>
<link href="https://fonts.googleapis.com/css2?family=Oswald:wght@300;400;600&family=Open+Sans:wght@400&display=swap" rel="stylesheet">
<style>
  :root {
    --page: #ffffff;
    --ink: #1a1a1a;
    --black: #000000;
    --cyan: #2aa3d4;
    --magenta: #e514d6;
    --box-blue: #29a9e1;
    --seal-top: #6b4fa8;
    --seal-top-back: #c98a45;
    --seal-bottom: #2e9e8e;
    --strip: rgba(255,255,255,0.35);
    --line: #d8d8d8;
    --soft-text: #e8e8e8;
  }
  * { box-sizing: border-box; margin: 0; padding: 0; }
  html, body { width: 1200px; height: 882px; overflow: hidden; background: var(--page); }
  .canvas { position: relative; width: 1200px; height: 882px; font-family: "Oswald", sans-serif; }

  .view-label { position: absolute; font-family: "Open Sans", sans-serif; font-size: 30px; color: var(--ink); line-height: 1; }

  .sachet { position: absolute; top: 114px; width: 316px; height: 740px; overflow: hidden; }
  .art-upper { position: absolute; left: 0; right: 0; top: 0; height: 256px; }
  .art-middle { position: absolute; left: 0; right: 0; top: 256px; height: 244px; }
  .art-lower { position: absolute; left: 0; right: 0; top: 500px; bottom: 0; }
  .seal { position: absolute; left: 0; right: 0; height: 60px;
    background-image: repeating-linear-gradient(0deg, rgba(255,255,255,0.18) 0 3px, transparent 3px 7px); }
  .seal.top { top: 0; background-color: var(--seal-top); }
  .seal.bottom { bottom: 0; background-color: var(--seal-bottom); }
  .label-band { position: absolute; left: 18px; right: 13px; top: 256px; height: 244px; background: var(--black); }

  .company { color: var(--magenta); font-weight: 400; text-transform: uppercase; letter-spacing: -0.3px; text-align: center; white-space: nowrap; }
  .product-name { color: var(--cyan); font-weight: 600; text-transform: uppercase; text-align: center; line-height: 0.95; }
  .tagline { position: absolute; left: 0; right: 0; text-align: center; font-weight: 300; text-transform: uppercase; color: var(--ink); }

  /* front */
  .front { left: 35px; }
  .front .art-upper { background: linear-gradient(180deg, #7b5cc8 0%, #c9a6dc 40%, #d9b48a 75%, #d7a05c 100%); }
  .front .art-middle { background: linear-gradient(90deg, #6a5aa8, #caa46e); }
  .front .art-lower { background: linear-gradient(180deg, #8fd3d8 0%, #d4dedb 45%, #d8cbb8 75%, #5ab8a4 100%); }
  .front .label-inner { position: absolute; inset: 0; display: flex; flex-direction: column; align-items: center; justify-content: center; gap: 10px; }
  .front .company { font-size: 17px; }
  .front .product-name { font-size: 50px; }
  .front .tagline { top: 510px; font-size: 30px; line-height: 38px; }

  /* back */
  .back { left: 428px; }
  .back .seal.top { background-color: var(--seal-top-back); }
  .back .art-upper { background: linear-gradient(180deg, #dba060 0%, #e8cdaa 40%, #b596cf 75%, #8e6ac2 100%); }
  .back .art-middle { background: linear-gradient(90deg, #c99a5a, #8e6ac2); }
  .back .art-lower { background: linear-gradient(180deg, #ebe6e1 0%, #e0d9d2 60%, #cbb9a6 85%, #5ab8a4 100%); }
  .back .label-band { left: 16px; right: 16px; }
  .back .mini-brand { position: absolute; left: 0; width: 116px; top: 46px; display: flex; flex-direction: column; align-items: center; gap: 4px; }
  .back .company { font-size: 7px; }
  .back .product-name { font-size: 20px; }
  .back .mini-tagline { position: absolute; left: 0; width: 116px; top: 148px; text-align: center; font-weight: 300; text-transform: uppercase; color: var(--soft-text); font-size: 12px; line-height: 16px; }
  .center-strip { position: absolute; top: 0; bottom: 0; left: 136px; width: 40px; background: var(--strip); }

  .nutrition { position: absolute; left: 128px; top: 34px; width: 142px; height: 160px; border: 1.5px solid var(--line); border-radius: 6px; padding: 8px 8px; color: var(--soft-text); font-family: "Open Sans", sans-serif; }
  .nutrition h3 { font-family: "Oswald", sans-serif; font-weight: 400; font-size: 17px; line-height: 1; border-bottom: 3px solid var(--line); padding-bottom: 3px; white-space: nowrap; }
  .nutrition .row { display: flex; justify-content: space-between; font-size: 4.5px; line-height: 7.2px; border-bottom: 0.5px solid #888; }
  .nutrition .row.thick { border-bottom: 2px solid var(--line); }
  .nutrition .note { font-size: 4px; line-height: 5px; margin-top: 3px; }
  .cert-name { position: absolute; left: 196px; top: 512px; width: 44px; text-align: center; font-weight: 600; font-size: 16px; line-height: 1; color: var(--ink); }

  /* outer box */
  .outer-box { position: absolute; left: 811px; top: 85px; width: 362px; height: 777px; overflow: hidden; }
  .outer-box .art-top { position: absolute; left: 0; right: 0; top: 0; height: 172px;
    background: linear-gradient(110deg, #4a52c9 0%, #9a5bc9 30%, #e98c9c 60%, #e7762a 100%); }
  .outer-box .art-bottom { position: absolute; left: 0; right: 0; top: 446px; bottom: 0;
    background: linear-gradient(135deg, #9fdff0 0%, #d8eee6 35%, #f3e2c2 70%, #aee0cf 100%); }
  .outer-box .label-band { left: 0; right: 0; top: 172px; height: 274px; display: flex; flex-direction: column; align-items: center; justify-content: center; gap: 14px; }
  .outer-box .company { font-size: 18px; }
  .outer-box .product-name { font-size: 58px; }
  .outer-box .tagline { top: 474px; font-size: 31px; line-height: 38.5px; }
  .count-badge { position: absolute; left: 119px; bottom: 0; width: 123px; height: 114px; background: var(--box-blue); color: #fff; text-align: center; }
  .count-badge .num { display: block; font-weight: 600; font-size: 60px; line-height: 1; margin-top: 16px; }
  .count-badge .unit { display: block; font-weight: 400; font-size: 20px; line-height: 1; margin-top: 2px; }
</style>
</head>
<body>
<div class="canvas">
  <span class="view-label" style="left:40px; top:58px;">front</span>
  <span class="view-label" style="left:436px; top:58px;">back</span>
  <span class="view-label" style="left:815px; top:30px;">outer box</span>

  <!-- Front of sachet -->
  <section class="sachet front">
    <div class="art-upper" role="img" aria-label="Soft purple and amber bokeh light background"></div>
    <div class="art-middle"></div>
    <div class="art-lower" role="img" aria-label="Soft aqua and cream bokeh light background"></div>
    <div class="seal top"></div>
    <div class="seal bottom"></div>
    <div class="label-band">
      <div class="label-inner">
        <p class="company">Lumora Products, Inc.</p>
        <p class="product-name">Lumora<br>Drink<br>Mix</p>
      </div>
    </div>
    <p class="tagline">Feel as good<br>tomorrow morning<br>as you do<br>tonight.</p>
  </section>

  <!-- Back of sachet -->
  <section class="sachet back">
    <div class="art-upper" role="img" aria-label="Soft orange and purple bokeh light background"></div>
    <div class="art-middle"></div>
    <div class="art-lower" role="img" aria-label="Soft cream light background"></div>
    <div class="seal top"></div>
    <div class="seal bottom"></div>
    <div class="label-band">
      <div class="mini-brand">
        <p class="company">Lumora Products, Inc.</p>
        <p class="product-name">Lumora<br>Drink<br>Mix</p>
      </div>
      <p class="mini-tagline">Feel as good<br>tomorrow morning<br>as you do<br>tonight.</p>
      <div class="nutrition">
        <h3>NUTRITION FACTS</h3>
        <div class="row"><span>Serving size</span><span>Per container</span></div>
        <div class="row thick"><span>Calories</span><span>0</span></div>
        <div class="row"><span></span><span>% Daily Value</span></div>
        <div class="row"><span>Total fat</span><span>0%</span></div>
        <div class="row"><span>Sodium</span><span>0%</span></div>
        <div class="row"><span>Total carbs</span><span>0%</span></div>
        <div class="row"><span>Sugars</span><span>0%</span></div>
        <div class="row thick"><span>Protein</span><span>0%</span></div>
        <div class="row"><span>Vitamin C</span><span>Zinc</span></div>
        <p class="note">Values based on a 2,000 calorie diet.</p>
      </div>
    </div>
    <div class="center-strip"></div>
    <p class="cert-name">NQB</p>
  </section>

  <!-- Outer box -->
  <section class="outer-box">
    <div class="art-top" role="img" aria-label="Blurred purple, pink and orange light background"></div>
    <div class="label-band">
      <p class="company">Lumora Products, Inc.</p>
      <p class="product-name">Lumora<br>Drink<br>Mix</p>
    </div>
    <div class="art-bottom" role="img" aria-label="Blurred aqua, cream and teal bokeh light background"></div>
    <p class="tagline">Feel as good<br>tomorrow morning<br>as you do<br>tonight.</p>
    <div class="count-badge"><span class="num">5</span><span class="unit">SACHETS</span></div>
  </section>
</div>
</body>
</html>
```